Thornbury Cafe Business Card

We are a café in Sydney.
see website for details. http://www.thornburycafe.com.au

want a single sided business card - no person's name on there.
This is to hand out to customers
use the attached logo

Industry/Entity Type

Business

Contact Information for Business Card

Thornbury Café
Mezzanine Level,
517-521 Kelvin St
Sydney NSW 2000
T: 9418 5063
W: www.thornburycafe.com.au
F: facebook.com/ThornburyCafeSydney

Catering Available
Phone for Lunchtime Bookings

```html
<!DOCTYPE html>
<html lang="en">
<head>
<meta charset="utf-8">
<title>Thornbury Cafe Business Card</title>
<link href="https://fonts.googleapis.com/css2?family=Quicksand:wght@400;500&family=Dancing+Script:wght@500&display=swap" rel="stylesheet">
<style>
  :root {
    --backdrop: #e9e6e1;
    --card: #222222;
    --card-edge: #2b2b2b;
    --ink: #f2f0ec;
    --ink-soft: #d8d5cf;
    --rust: #b8643a;
    --name: #f2f0ec;
  }
  * { margin: 0; padding: 0; box-sizing: border-box; }
  html, body {
    width: 1200px;
    height: 837px;
    overflow: hidden;
    background: var(--backdrop);
  }
  .canvas {
    width: 1200px;
    height: 837px;
    display: flex;
    align-items: center;
    justify-content: center;
  }
  .card {
    position: relative;
    width: 1000px;
    height: 572px;
    background: radial-gradient(ellipse at 50% 40%, var(--card-edge), var(--card));
    box-shadow: 0 10px 30px rgba(0, 0, 0, 0.25);
    color: var(--ink);
    font-family: "Quicksand", sans-serif;
  }
  .brand {
    position: absolute;
    top: 170px;
    left: 0;
    right: 0;
    display: flex;
    align-items: center;
    justify-content: center;
    gap: 26px;
  }
  .brand-dot {
    width: 72px;
    height: 72px;
    border-radius: 50%;
    background: var(--rust);
    flex: none;
  }
  .brand-name {
    font-family: "Quicksand", sans-serif;
    font-weight: 500;
    font-size: 64px;
    letter-spacing: 3px;
    color: var(--name);
    text-transform: uppercase;
  }
  .tagline {
    position: absolute;
    top: 280px;
    left: 0;
    right: 0;
    text-align: center;
    font-family: "Dancing Script", cursive;
    font-size: 40px;
    color: var(--ink-soft);
    letter-spacing: 1px;
  }
  .address {
    position: absolute;
    left: 48px;
    bottom: 44px;
    display: flex;
    align-items: center;
    gap: 10px;
    font-size: 19px;
    letter-spacing: 1.2px;
    color: var(--ink-soft);
  }
  .contact {
    position: absolute;
    right: 48px;
    bottom: 38px;
    text-align: right;
    font-size: 19px;
    letter-spacing: 1.2px;
    line-height: 1.55;
    color: var(--ink-soft);
  }
  .contact-heading {
    font-size: 24px;
    font-weight: 500;
    color: var(--ink);
    letter-spacing: 1.5px;
  }
  .contact-line {
    display: flex;
    align-items: center;
    justify-content: flex-end;
    gap: 10px;
  }
  .contact-line.phone { justify-content: flex-start; margin-top: 6px; }
  .marker {
    width: 16px;
    height: 16px;
    border-radius: 50%;
    background: var(--ink-soft);
    flex: none;
  }
  .icon { width: 20px; height: 20px; flex: none; }
</style>
</head>
<body>
<main class="canvas">
  <article class="card">
    <div class="brand">
      <span class="brand-dot"></span>
      <span class="brand-name">Thornbury Cafe</span>
    </div>
    <p class="tagline">- The Hidden Table -</p>

    <p class="address">
      <svg class="icon" viewBox="0 0 20 20" aria-hidden="true">
        <path d="M10 1.5a6 6 0 0 0-6 6c0 4.5 6 11 6 11s6-6.5 6-11a6 6 0 0 0-6-6z" fill="none" stroke="#d8d5cf" stroke-width="1.8"/>
        <circle cx="10" cy="7.5" r="2.2" fill="#d8d5cf"/>
      </svg>
      517-521 Kelvin St, Sydney, Mezzanine level
    </p>

    <div class="contact">
      <p class="contact-heading">Order online:</p>
      <p class="contact-line">www.thornburycafe.com.au <span class="marker"></span></p>
      <p class="contact-line">facebook.com/thornburycafesydney <span class="marker"></span></p>
      <p class="contact-line phone">
        <svg class="icon" viewBox="0 0 20 20" aria-hidden="true">
          <circle cx="10" cy="10" r="9" fill="#d8d5cf"/>
          <path d="M7 5.5l1.6 2.4-1 1.1a6 6 0 0 0 3.4 3.4l1.1-1 2.4 1.6-.8 1.6c-3.8-.3-7.1-3.6-7.4-7.4z" fill="#222222"/>
        </svg>
        +612 9418 5063
      </p>
    </div>
  </article>
</main>
</body>
</html>
```